Business card design needed

Family General Practitioner/ Family Physician.
Logo is the logo of the Noble Guild of Family Healers Oceania
http://kpltw.varendo.example/ImageShelf/marks/pages/NGFHO%20mark_jpg.htm
Updates

Project Deadline Extended
Reason: Just a bit more time to make changes and the weekend for me to look at things closely and to choose. Thanks, Orin

Thanks for all the submissions. So many of them are really works of art. Not one of them are not good. The ones that I am eliminating are the ones that I think are not suitable for me personally only, and because if I don't, it makes it very difficult to decide as many of you are also sending me slight variations of a card. I have just decided to choose a second place card too. Can't thank you all enough. Good luck, Orin. P.S - Working today till 10 pm as the card says :-), so probably won't be able to give a feedback till late Saturday night or Sunday morning here in Sydney, Australia. 

Project Deadline Extended
Reason: Just added a second place to the budget and realised that Australia is ahead of the rest of the world in the time zone (only :-) - don't want to offend anyone or start a debate!! ) , so Monday deadline will mean it will be a weekend for the rest of the world. Just wanted to give everyone more time to submit their best, especially since I will be picking a second card too. Can't thank everyone enough for the submissions. P.S - Not keen on photos on the card.

Industry/Entity Type

Business

Contact Information for Business Card

Dr. Orin Halvey M.B.B.S., F.N.G.F.H.O
Family General Practitioner
Address, timings, phone and fax number on the back.

Requirements
Must have
• Timings
Mon 7 am - 7 pm
Tues 7 am - 12 pm
Wed 7 am - 10 pm
Thurs 7 am - 12 pm
Fri 7 am - 8 pm
Sat 8 am - 10 pm
Sun - Off

```html
<!DOCTYPE html>
<html lang="en">
<head>
<meta charset="utf-8">
<title>Dr. Orin Halvey – Business Card</title>
<link rel="stylesheet" href="https://fonts.googleapis.com/css2?family=Source+Sans+3:wght@400;600&display=swap">
<style>
  :root {
    --stage: #eeeae4;
    --brand-blue: #1b87b9;
    --card-white: #ffffff;
    --ink: #222222;
    --text-on-blue: #ffffff;
    --faint-mark: #e9e9e9;
  }
  * { box-sizing: border-box; margin: 0; padding: 0; }
  html, body {
    width: 1200px; height: 378px; overflow: hidden;
    background: var(--stage);
    font-family: "Source Sans 3", sans-serif;
  }
  .stage { position: relative; width: 1200px; height: 378px; }
  .card {
    position: absolute; top: 38px; width: 540px; height: 307px;
    box-shadow: 0 2px 6px rgba(0,0,0,0.18);
    overflow: hidden;
  }
  .card--front { left: 38px; background: var(--brand-blue); color: var(--text-on-blue); }
  .card--back { left: 610px; background: var(--card-white); color: var(--ink); }

  .guild-mark {
    position: absolute; left: 30px; top: 92px; width: 170px;
    display: flex; flex-direction: column; align-items: center; gap: 10px;
    text-align: center; font-size: 15px; line-height: 1.25; font-weight: 400;
  }
  .guild-mark__dot { width: 34px; height: 34px; border-radius: 50%; background: currentColor; }

  .identity { position: absolute; left: 228px; width: 270px; top: 84px; text-align: center; }
  .identity__name { font-size: 35px; font-weight: 400; line-height: 1; letter-spacing: 0.2px; }
  .identity__creds { font-size: 12px; margin-top: 17px; letter-spacing: 0.3px; }
  .identity__rule { height: 3px; background: var(--text-on-blue); margin: 24px 0 13px; }
  .identity__role { font-size: 17px; }

  .hours { position: absolute; left: 56px; top: 47px; }
  .hours__title { font-size: 22px; font-weight: 400; margin-left: 38px; margin-bottom: 16px; }
  .hours__table { border-collapse: collapse; font-size: 12.5px; line-height: 15.5px; }
  .hours__table td { padding: 0; }
  .hours__day { width: 74px; }
  .hours__sep { width: 18px; }

  .guild-mark--faint {
    left: 318px; top: 80px; width: 160px; color: var(--faint-mark); font-size: 16px;
  }

  .contact-band {
    position: absolute; left: 0; bottom: 0; width: 100%; height: 77px;
    background: var(--brand-blue); color: var(--text-on-blue);
    text-align: center; font-size: 13px; line-height: 18px; padding-top: 22px;
  }
  .contact-band__label { font-weight: 600; }
  .contact-band__phones { font-size: 14px; }
</style>
</head>
<body>
<main class="stage">
  <section class="card card--front">
    <div class="guild-mark">
      <span class="guild-mark__dot"></span>
      <span>Noble Guild of Family Healers Oceania</span>
    </div>
    <div class="identity">
      <h1 class="identity__name">Dr. Orin Halvey</h1>
      <p class="identity__creds">M.B.B.S., F.N.G.F.H.O</p>
      <div class="identity__rule"></div>
      <p class="identity__role">Family General Practitioner</p>
    </div>
  </section>

  <section class="card card--back">
    <div class="hours">
      <h2 class="hours__title">Timing</h2>
      <table class="hours__table">
        <tr><td class="hours__day">Monday</td><td class="hours__sep">:</td><td>7 AM -&nbsp;&nbsp; 7 PM</td></tr>
        <tr><td class="hours__day">Tuesday</td><td class="hours__sep">:</td><td>7 AM - 12 PM</td></tr>
        <tr><td class="hours__day">Wednesday</td><td class="hours__sep">:</td><td>7 AM - 10 PM</td></tr>
        <tr><td class="hours__day">Thursday</td><td class="hours__sep">:</td><td>7 AM - 12 PM</td></tr>
        <tr><td class="hours__day">Friday</td><td class="hours__sep">:</td><td>7 AM -&nbsp;&nbsp; 8 PM</td></tr>
        <tr><td class="hours__day">Saturday</td><td class="hours__sep">:</td><td>8 AM - 10 PM</td></tr>
        <tr><td class="hours__day">Sunday</td><td class="hours__sep">:</td><td>OFF</td></tr>
      </table>
    </div>
    <div class="guild-mark guild-mark--faint" aria-hidden="true">
      <span class="guild-mark__dot"></span>
      <span>Noble Guild of Family Healers Oceania</span>
    </div>
    <div class="contact-band">
      <p>Upper Level, Linden Arcade, Marrowgate Shopping Centre, Hollis Ridge, NSW 2199</p>
      <p class="contact-band__phones"><span class="contact-band__label">P :</span> 02 5550 1840&nbsp; <span class="contact-band__label">F :</span> 02 5550 1877</p>
    </div>
  </section>
</main>
</body>
</html>
```